Textbook cover for educational dental hygiene seminar

A professional and trendy textbook cover design to be used. 8.5 x 11 with full bleed, cmyk, and a count for binding when designed. Year 2023 displayed, and title BexlerRDH’s Dental Hygiene Academy. Colors- shades of purple, white, and black. Please also use logo. Website www.BexlerRDHExamPrep.example

For background- maybe ombré, or some sort of trendy design. Display a big tooth on the front.

Colors
6B429C
8869AF
B7A5CE
E3DAEB
F3F0F8

```html
<!DOCTYPE html>
<html lang="en">
<head>
<meta charset="utf-8">
<title>BexlerRDH’s Dental Hygiene Academy – Cover Spread</title>
<link href="https://fonts.googleapis.com/css2?family=Montserrat:wght@400;500;600;800&family=Source+Sans+3:wght@400&display=swap" rel="stylesheet">
<style>
  :root {
    --purple-deep: #2c0a32;
    --purple-dark: #43134d;
    --purple-mid: #5a1f66;
    --purple-brand: #6B429C;
    --purple-soft: #8869AF;
    --lilac: #B7A5CE;
    --lilac-pale: #E3DAEB;
    --white: #ffffff;
    --ink: #1e0a22;
    --stage: #f2f2f2;
    --head: "Montserrat", sans-serif;
    --body: "Source Sans 3", sans-serif;
  }
  * { margin: 0; padding: 0; box-sizing: border-box; }
  html, body { width: 1200px; height: 475px; overflow: hidden; }
  body { background: var(--stage); position: relative; font-family: var(--body); }

  .spread { position: absolute; left: 0; top: 0; width: 776px; height: 475px; }

  /* back cover */
  .back-cover {
    position: absolute; left: 0; top: 0; width: 373px; height: 475px;
    background: linear-gradient(160deg, var(--purple-mid) 0%, var(--purple-dark) 45%, var(--purple-deep) 100%);
    overflow: hidden;
  }
  .author-photo {
    position: absolute; left: 228px; top: 28px; width: 126px; height: 205px;
    background: radial-gradient(ellipse at 50% 25%, #7a4f4a 0%, #2a1c26 45%, #1a1020 100%);
    border-radius: 40% 40% 4px 4px / 25% 25% 4px 4px;
  }
  .back-title { position: absolute; left: 34px; top: 36px; color: var(--white); z-index: 1; }
  .title-name { font-family: var(--head); font-weight: 800; line-height: 1; letter-spacing: -0.3px; white-space: nowrap; }
  .title-line { font-family: var(--head); font-weight: 500; line-height: 1; white-space: nowrap; }
  .title-academy { font-family: var(--head); font-weight: 400; line-height: 1; display: flex; align-items: center; white-space: nowrap; }
  .year-bar {
    display: flex; justify-content: flex-end; align-items: center;
    background: linear-gradient(90deg, rgba(255,255,255,0) 0%, var(--lilac-pale) 45%, var(--white) 60%);
    color: var(--ink); font-family: var(--head); font-weight: 600;
  }
  .back-title .title-name { font-size: 26px; }
  .back-title .title-line { font-size: 19px; margin-top: 6px; }
  .back-title .title-academy { font-size: 19px; margin-top: 6px; }
  .back-title .year-bar { width: 78px; height: 15px; margin-left: 8px; font-size: 12px; padding-right: 4px; }

  .blurb {
    position: absolute; left: 34px; color: var(--white);
    font-size: 8px; line-height: 12px; text-align: justify;
  }
  .blurb-short { top: 124px; width: 147px; }
  .blurb-long { top: 255px; width: 299px; }

  .brand-mark {
    position: absolute; display: flex; align-items: center; gap: 5px;
    color: var(--white); font-family: var(--head); font-weight: 600; white-space: nowrap;
  }
  .brand-dot { border-radius: 50%; background: var(--purple-brand); border: 2px solid var(--white); flex: none; }
  .back-cover .brand-mark { left: 30px; top: 410px; font-size: 11px; }
  .back-cover .brand-dot { width: 26px; height: 26px; }

  /* spine */
  .spine {
    position: absolute; left: 373px; top: 0; width: 37px; height: 475px;
    background: linear-gradient(180deg, var(--purple-dark), var(--purple-deep));
  }
  .spine-title {
    position: absolute; left: 11px; top: 34px; writing-mode: vertical-rl;
    font-family: var(--head); font-weight: 500; font-size: 12.5px; color: var(--white);
    letter-spacing: 0.2px; white-space: nowrap;
  }
  .spine-title strong { font-weight: 800; }
  .spine-year {
    position: absolute; left: 6px; top: 338px; width: 19px; height: 68px;
    background: linear-gradient(180deg, rgba(255,255,255,0) 0%, var(--white) 30%);
    writing-mode: vertical-rl; display: flex; align-items: flex-end; justify-content: center;
    font-family: var(--head); font-weight: 800; font-size: 12px; color: var(--ink); padding-bottom: 3px;
  }
  .spine-dot {
    position: absolute; left: 10px; top: 427px; width: 17px; height: 17px;
    border-radius: 50%; background: var(--purple-brand); border: 2px solid var(--white);
  }

  /* front cover */
  .front-cover {
    position: absolute; left: 410px; top: 0; width: 366px; height: 475px;
    background: linear-gradient(180deg, var(--purple-dark) 0%, #3a0f42 100%);
    overflow: hidden;
  }
  .front-title { position: absolute; left: 26px; top: 36px; width: 314px; color: var(--white); }
  .front-title .title-name { font-size: 40px; }
  .front-title .title-line { font-size: 33px; margin-top: 10px; }
  .front-title .title-academy { font-size: 33px; margin-top: 10px; }
  .front-title .year-bar { width: 122px; height: 25px; margin-left: auto; font-size: 20px; padding-right: 6px; }

  .cover-photo {
    position: absolute; left: 0; top: 179px; width: 366px; height: 243px;
    background:
      radial-gradient(ellipse at 53% 78%, #f4f4f6 0%, rgba(244,244,246,0) 14%),
      radial-gradient(ellipse at 50% 45%, #d9b8a6 0%, rgba(217,184,166,0) 35%),
      linear-gradient(180deg, #a8bbd4 0%, #8ea2bf 55%, #5a4a78 100%);
  }
  .photo-fade {
    position: absolute; left: 0; top: 350px; width: 366px; height: 72px;
    background: linear-gradient(180deg, rgba(58,15,66,0) 0%, rgba(58,15,66,0.85) 100%);
  }
  .front-cover .brand-mark { left: 138px; top: 402px; font-size: 14px; }
  .front-cover .brand-dot { width: 30px; height: 30px; }
</style>
</head>
<body>
  <main class="spread">
    <section class="back-cover">
      <div class="author-photo" role="img" aria-label="Portrait photo of the author in a dark suit with arms crossed"></div>
      <header class="back-title">
        <div class="title-name">BexlerRDH’S</div>
        <div class="title-line">DENTAL HYGIENE</div>
        <div class="title-academy">ACADEMY <span class="year-bar">2023</span></div>
      </header>
      <p class="blurb blurb-short">Lorem ipsum dolor sit amet, consectetur adipiscing elit, sed do eiusmod tempor incididunt ut labore et dolore magna aliqua. Quis ipsum suspendisse ultrices gravida. Risus commodo viverra maecenas accumsan lacus vel facilisis. Lorem ipsum dolor sit amet, consectetur adipiscing elit, sed do eiusmod tempor incididunt ut labore et dolore magna aliqua. Quis ipsum suspendisse.</p>
      <p class="blurb blurb-long">Lorem ipsum dolor sit amet, consectetur adipiscing elit, sed do eiusmod tempor incididunt ut labore et dolore magna aliqua. Quis ipsum suspendisse ultrices gravida. Risus commodo viverra maecenas accumsan lacus vel facilisis. Lorem ipsum dolor sit amet, consectetur adipiscing elit, sed do eiusmod tempor incididunt ut labore et dolore magna aliqua. Quis ipsum suspendisse ultrices gravida. Risus commodo viverra maecenas accumsan lacus vel facilisis. Lorem ipsum dolor sit amet, consectetur adipiscing elit, sed do eiusmod tempor incididunt ut labore et dolore magna aliqua. Quis ipsum suspendisse ultrices gravida. Risus commodo viverra maecenas accumsan lacus vel facilisis. Lorem ipsum dolor sit amet, consectetur adipiscing elit, sed do eiusmod tempor incididunt ut labore et dolore magna aliqua. Quis ipsum suspendisse ultrices gravida. Risus commodo viverra maecenas accumsan lacus vel facilisis.</p>
      <div class="brand-mark"><span class="brand-dot"></span>BexlerRDH</div>
    </section>

    <section class="spine">
      <div class="spine-title"><strong>BexlerRDH’S</strong> DENTAL HYGIENE ACADEMY</div>
      <div class="spine-year">2023</div>
      <div class="spine-dot"></div>
    </section>

    <section class="front-cover">
      <header class="front-title">
        <div class="title-name">BexlerRDH’S</div>
        <div class="title-line">DENTAL HYGIENE</div>
        <div class="title-academy">ACADEMY <span class="year-bar">2023</span></div>
      </header>
      <div class="cover-photo" role="img" aria-label="Photo of two hands sheltering a large white tooth model on a table"></div>
      <div class="photo-fade"></div>
      <div class="brand-mark"><span class="brand-dot"></span>BexlerRDH</div>
    </section>
  </main>
</body>
</html>
```